Business Card Design for DMV business in Las Vegas, NV - (Very open to design ideas and colors)

We are looking for a business card design for a new company in Las Vegas, NV called Quickline Tag Services. This company is here to give the general public the option of using our services, for a fee, instead of the customer sitting and waiting at a Silverpine Motor Bureau office for 3-6 hours on average. Our business will process vehicle registrations, titles, plates, handicap placards, temporary moving permits, etc. in a fraction of the time compared to the DMV's standard wait times (3-6 hours) hence our business name Quickline Tag SERVICES. Our business will be capable of handling just about any DMV related issue and this will keep our customers happier if our customer never has to show up to the DMV and we do all the work for them. I am very open to design ideas and colors for the business card. One thing that I am looking for is something that catches the eye fast but conveys the message about our business being able to expedite a customer's needs quickly and efficiently. You may modify the wording to say Quickline Tag Services or make SERVICES capitalized. I look forward to reviewing your design ideas. If you want to get ideas about the Silverpine Motor Bureau please visit www.spmotorbureau.org. This is the Silverpine Motor Bureau's official website.
Business
Quickline Tag Services, LLCRyan Steeps - OwnerEmail - NevadaDMVExpress@gmail.comWebsite - NevadaDMVExpress.comPhone # 702-555-0147

```html
<!DOCTYPE html>
<html lang="en">
<head>
<meta charset="UTF-8">
<title>Quickline Tag Services – Business Card</title>
<link rel="stylesheet" href="https://fonts.googleapis.com/css2?family=Cormorant+Garamond:wght@700&family=Tinos&display=swap">
<style>
  :root {
    --card-blue: #0b4f7a;
    --ink-white: #ffffff;
  }
  html, body {
    margin: 0;
    padding: 0;
    width: 1200px;
    height: 702px;
    overflow: hidden;
    background: var(--card-blue);
  }
  .card {
    position: relative;
    width: 1200px;
    height: 702px;
    background: var(--card-blue);
    color: var(--ink-white);
  }
  .card__title {
    position: absolute;
    top: 178px;
    left: 0;
    width: 100%;
    margin: 0;
    text-align: center;
    font-family: "Cormorant Garamond", serif;
    font-weight: 700;
    font-size: 38px;
    font-variant: small-caps;
    letter-spacing: 0.1em;
    line-height: 1;
  }
  .card__rule {
    position: absolute;
    top: 266px;
    left: 256px;
    width: 686px;
    height: 16px;
  }
  .card__contacts {
    position: absolute;
    top: 330px;
    left: 0;
    width: 100%;
    margin: 0;
    padding: 0;
    list-style: none;
    text-align: center;
    font-family: "Tinos", serif;
    font-size: 40px;
    line-height: 66px;
  }
</style>
</head>
<body>
  <main class="card">
    <h1 class="card__title">Quickline Tag Services, LLC Colin</h1>
    <svg class="card__rule" viewBox="0 0 686 16" aria-hidden="true">
      <path d="M0 8 Q343 1 686 8 Q343 12 0 8 Z" fill="var(--ink-white)"/>
    </svg>
    <ul class="card__contacts">
      <li class="card__email">QuicklineTagServices@tagmailbox.net</li>
      <li class="card__website">QuicklineTagServices.com</li>
      <li class="card__phone">702-555-0147</li>
    </ul>
  </main>
</body>
</html>
```